Grovecraft Lip Balm. It is formulated with men in mind but other people certainly can use it.

The over arching name of the project is Tharn - which needs to be in the label somewhere, but Grovecraft is the title.
It would be for a round jar container.
It is out of promoting products for men to open discussion about health issues that men often not talk about. As each product is created it will have a message to men about the health issue and where to find information, seek help or just be able to talk about it.
I would like darker colours (black) as the base but using other colours to
for the wording and design.
I am open to ideas on the layout, I have included some ideas, and also some of my own labelling ideas that I have worked on. I do like the carbon fibre background look that I have for my tharn label. I have also included my wevnu label with some colour ideas.
I also was wondering about making it a after tattoo balm so that it can also be used as a lip balm as well…two for the price of one..basically the same ingredients are used.
They may change the look of the intended artwork..but I leave it in your skill full hands.
My number is +61498152073. You can txt me if you need some clarification.
Thank you
Kind regards and blessings

Target Market(s)

Target market is men of all ages as they can all be affected by one health issue or another at different times of life

Industry/Entity Type

Healthcare and beauty

Font styles to use
Sans Serif
Decorative

Requirements
Must have
• I still need to indeed to ingredients and container size.
Nice to have
• A novel and different look from the usual crowd that try to hard to look cool or funky

```html
<!DOCTYPE html>
<html lang="en">
<head>
<meta charset="utf-8">
<title>Tharn Grovecraft Lip Balm – Label Set</title>
<link rel="stylesheet" href="https://fonts.googleapis.com/css2?family=Oswald:wght@500&family=Montserrat:wght@600;700&display=swap">
<style>
  :root {
    --backdrop: #67635c;
    --label-black: #0c0c0c;
    --label-charcoal: #2a2a2a;
    --amber: #c27a22;
    --amber-deep: #8a4410;
    --silver: #dcdcdc;
    --white: #f2f2f2;
    --rule: #9a9a9a;
  }
  * { margin: 0; padding: 0; box-sizing: border-box; }
  html, body {
    width: 1200px; height: 900px; overflow: hidden;
    background: var(--backdrop);
  }
  .canvas { position: relative; width: 1200px; height: 900px; }

  /* shared text styles */
  .brand {
    font-family: "Montserrat", sans-serif; font-weight: 700;
    color: var(--silver); letter-spacing: 1px; text-align: center;
  }
  .product-title {
    font-family: "Oswald", sans-serif; font-weight: 500;
    color: var(--amber); text-align: center; line-height: 1;
    letter-spacing: 3px;
  }
  .product-type {
    display: flex; align-items: center; justify-content: center; gap: 14px;
    font-family: "Montserrat", sans-serif; font-weight: 600;
    color: var(--white);
  }
  .product-type::before, .product-type::after {
    content: ""; height: 1px; background: var(--rule);
  }
  .volume {
    font-family: "Montserrat", sans-serif; font-weight: 700;
    text-align: center;
  }

  /* wrap label for the jar side */
  .side-label {
    position: absolute; left: 70px; top: 300px; width: 540px; height: 300px;
    background: radial-gradient(ellipse at 50% 25%, var(--label-charcoal), var(--label-black) 70%);
    overflow: hidden;
  }
  .side-label .brand { position: absolute; top: 34px; width: 100%; font-size: 44px; }
  .side-label .product-title { position: absolute; top: 104px; width: 100%; font-size: 62px; }
  .side-label .product-type {
    position: absolute; top: 184px; width: 100%;
    font-size: 15px; letter-spacing: 9px;
  }
  .side-label .product-type::before, .side-label .product-type::after { width: 74px; }
  .claims {
    position: absolute; top: 214px; width: 100%;
    display: flex; justify-content: center; align-items: center; gap: 26px;
  }
  .claim-badge {
    width: 36px; height: 36px; border-radius: 50%;
    border: 1.5px solid var(--amber);
  }
  .claim-divider { width: 1px; height: 42px; background: var(--rule); }
  .side-trim { position: absolute; left: 0; bottom: 0; width: 540px; height: 34px; }
  .side-label .volume {
    position: absolute; bottom: 10px; width: 100%;
    font-size: 14px; color: var(--label-black);
  }

  /* round lid label */
  .lid-label {
    position: absolute; left: 640px; top: 220px; width: 470px; height: 470px;
    border-radius: 50%;
    background: radial-gradient(circle at 50% 35%, var(--label-charcoal), var(--label-black) 65%);
    box-shadow: 0 0 0 2px #1a1a1a;
  }
  .lid-label .brand { position: absolute; top: 92px; width: 100%; font-size: 64px; }
  .lid-label .product-title { position: absolute; top: 198px; width: 100%; font-size: 78px; }
  .lid-label .product-type {
    position: absolute; top: 310px; width: 100%;
    font-size: 18px; letter-spacing: 12px;
  }
  .lid-label .product-type::before, .lid-label .product-type::after { width: 92px; }
  .lid-label .volume {
    position: absolute; top: 394px; width: 100%;
    font-size: 22px; color: var(--white);
  }
</style>
</head>
<body>
<main class="canvas">

  <section class="side-label" aria-label="Jar wrap label">
    <p class="brand">THARN</p>
    <h1 class="product-title">GROVECRAFT</h1>
    <p class="product-type">LIP BALM</p>
    <div class="claims">
      <span class="claim-badge"></span>
      <span class="claim-divider"></span>
      <span class="claim-badge"></span>
      <span class="claim-divider"></span>
      <span class="claim-badge"></span>
    </div>
    <svg class="side-trim" viewBox="0 0 540 34" aria-hidden="true">
      <rect x="0" y="16" width="540" height="3" fill="#cfcfcf"/>
      <rect x="0" y="22" width="540" height="6" fill="#c27a22"/>
      <polygon points="228,6 312,6 320,28 220,28" fill="#c27a22"/>
    </svg>
    <p class="volume">50ML</p>
  </section>

  <section class="lid-label" aria-label="Jar lid label">
    <p class="brand">THARN</p>
    <h2 class="product-title">GROVECRAFT</h2>
    <p class="product-type">LIP BALM</p>
    <p class="volume">50ML</p>
  </section>

</main>
</body>
</html>
```